A new presentation to our clients

we are a Real Estate agency, our website is www.lumibrasa.com and it’s time to have a new, fashion and remarcable Business Card. we want to differentiate ourselves from other companies so we want a business card that differentiates us. we want the business card to impact our customers. in the competitive market that we have today, we have to be different and it is this difference that we seek

Target Market(s)

Real Estate Clients

Contact Information for Business Card

We search a totaly diferent card from the usual

Font styles to use
Sans Serif

Colors
e34197

Requirements
Must have
• Logo, adress, phone contact, e-mail, photo, and our website
Nice to have
• We would like to see a modern business card
Should not have
• Houses or building draws

```html
<!DOCTYPE html>
<html lang="pt">
<head>
<meta charset="UTF-8">
<title>Lumi Brasa — Business Card</title>
<link rel="stylesheet" href="https://fonts.googleapis.com/css2?family=Oswald:wght@500&family=Work+Sans:wght@400;600&display=swap">
<style>
  :root {
    --page-bg: #1b1b1b;
    --card-dark: #141414;
    --card-mid: #262626;
    --brand-pink: #e34197;
    --text-light: #f2f2f2;
    --photo-top: #4a4744;
    --photo-mid: #3a3d47;
    --photo-jacket: #232a3a;
    --photo-deep: #1b2131;
  }
  * { box-sizing: border-box; margin: 0; padding: 0; }
  html, body { width: 1200px; height: 900px; overflow: hidden; }
  body {
    background: radial-gradient(ellipse at 50% 40%, #2a2a2a 0%, var(--page-bg) 70%);
    font-family: "Work Sans", Arial, sans-serif;
    color: var(--text-light);
    position: relative;
  }
  .card {
    position: absolute;
    left: 270px;
    width: 660px;
    height: 377px;
    background: linear-gradient(135deg, var(--card-dark) 0%, var(--card-mid) 70%, #1c1c1c 100%);
    box-shadow: 0 18px 40px rgba(0,0,0,0.6);
    overflow: hidden;
  }
  .card--front { top: 52px; }
  .card--back { top: 471px; }

  .brand-name {
    position: absolute;
    left: 62px;
    top: 168px;
    font-family: "Work Sans", Arial, sans-serif;
    font-weight: 600;
    font-size: 56px;
    line-height: 1;
    letter-spacing: 1px;
    color: var(--brand-pink);
  }
  .portrait {
    position: absolute;
    right: 0;
    top: 0;
    width: 300px;
    height: 100%;
    background: linear-gradient(180deg,
      var(--photo-top) 0%,
      var(--photo-mid) 45%,
      var(--photo-jacket) 72%,
      var(--photo-deep) 100%);
    -webkit-mask-image: linear-gradient(90deg, transparent 0%, #000 30%);
    mask-image: linear-gradient(90deg, transparent 0%, #000 30%);
  }

  .identity {
    position: absolute;
    right: 372px;
    top: 120px;
    text-align: right;
  }
  .identity__name {
    font-family: "Oswald", "Arial Narrow", sans-serif;
    font-weight: 500;
    font-size: 42px;
    line-height: 1;
    color: var(--brand-pink);
    text-transform: uppercase;
  }
  .identity__role {
    font-size: 19px;
    margin-top: 6px;
  }
  .divider {
    position: absolute;
    left: 305px;
    top: 120px;
    width: 2px;
    height: 92px;
    background: var(--brand-pink);
  }
  .contacts {
    position: absolute;
    left: 330px;
    top: 118px;
    list-style: none;
  }
  .contacts li {
    display: flex;
    align-items: center;
    gap: 10px;
    font-size: 19px;
    line-height: 24px;
  }
  .contacts svg { width: 12px; height: 12px; flex: none; }
  .address {
    position: absolute;
    left: 0;
    right: 0;
    top: 292px;
    text-align: center;
    font-size: 19px;
    letter-spacing: 0.3px;
  }
</style>
</head>
<body>
  <section class="card card--front">
    <div class="brand-name">Lumi Brasa</div>
    <div class="portrait" role="img" aria-label="Portrait photo of the agency director"></div>
  </section>

  <section class="card card--back">
    <div class="identity">
      <div class="identity__name">Helena Duarte</div>
      <div class="identity__role">Director</div>
    </div>
    <div class="divider"></div>
    <ul class="contacts">
      <li>
        <svg viewBox="0 0 12 12" aria-hidden="true"><path d="M2.5 1 L4.5 1 L5.2 3.6 L3.9 4.6 Q5 7 7.4 8.1 L8.4 6.8 L11 7.5 L11 9.5 Q10.5 11 9 11 Q1 10 1 3 Q1 1.5 2.5 1 Z" fill="var(--brand-pink)"/></svg>
        (+351) 221 480 362
      </li>
      <li>
        <svg viewBox="0 0 12 12" aria-hidden="true"><rect x="3" y="1" width="6" height="3" fill="var(--brand-pink)"/><rect x="1" y="4.5" width="10" height="4" rx="1" fill="var(--brand-pink)"/><rect x="3" y="8" width="6" height="3" fill="var(--brand-pink)"/></svg>
        (+351) 221 480 369
      </li>
      <li>
        <svg viewBox="0 0 12 12" aria-hidden="true"><rect x="1" y="2.5" width="10" height="7" fill="none" stroke="var(--brand-pink)" stroke-width="1.2"/><path d="M1 2.5 L6 6.5 L11 2.5" fill="none" stroke="var(--brand-pink)" stroke-width="1.2"/></svg>
        geral@lumibrasa.com
      </li>
      <li>
        <svg viewBox="0 0 12 12" aria-hidden="true"><g fill="none" stroke="var(--brand-pink)" stroke-width="1"><circle cx="6" cy="6" r="5"/><ellipse cx="6" cy="6" rx="2.2" ry="5"/><path d="M1 6 H11 M2 3.5 H10 M2 8.5 H10"/></g></svg>
        www.lumibrasa.com
      </li>
    </ul>
    <p class="address">Rua das Camélias, 58 4150-210, Porto Alto</p>
  </section>
</body>
</html>
```